We need a business card design, letterhead design and envelope design for our corporate image

We are looking for a corporate business card design, letterhead and envelope design to match the business card design. Logo is done.

```html
<!DOCTYPE html>
<html lang="en">
<head>
<meta charset="utf-8">
<title>Norvane business card</title>
<link rel="stylesheet" href="https://fonts.googleapis.com/css2?family=Open+Sans:wght@400;600;700&display=swap">
<style>
  :root {
    --backdrop: #e4e4e2;
    --paper: #fbfbfa;
    --ink: #5a5b5d;
    --accent: #f2bd00;
    --slate: #6b6c6e;
    --slate-light: #7a7b7d;
    --white: #ffffff;
  }
  * { margin: 0; padding: 0; box-sizing: border-box; }
  html, body { width: 1200px; height: 801px; overflow: hidden; }
  body {
    background: var(--backdrop);
    font-family: "Open Sans", Arial, sans-serif;
    color: var(--ink);
    position: relative;
  }
  .card {
    position: absolute;
    top: 252px;
    width: 520px;
    height: 297px;
    box-shadow: 0 6px 18px rgba(0,0,0,0.12);
  }
  .card-front { left: 50px; background: var(--paper); }
  .card-back { left: 630px; background: var(--slate); overflow: hidden; }

  .brand { position: absolute; display: flex; align-items: center; gap: 12px; }
  .brand-square { width: 30px; height: 30px; border: 4px solid var(--accent); }
  .brand-name { font-weight: 700; font-size: 34px; letter-spacing: -0.5px; line-height: 1; }
  .card-front .brand { left: 46px; top: 70px; }
  .card-front .brand-name { color: var(--ink); }

  .holder { position: absolute; right: 34px; top: 44px; text-align: right; }
  .holder-name { color: var(--accent); font-weight: 700; font-size: 17px; letter-spacing: 0.5px; }
  .holder-role { font-size: 12px; margin-top: 1px; }

  .divider { position: absolute; left: 34px; right: 34px; top: 168px; height: 1.5px; background: var(--accent); }

  .contact-list { position: absolute; left: 34px; top: 184px; list-style: none; font-size: 12.5px; line-height: 21px; }
  .contact-list li { display: flex; align-items: center; gap: 8px; }
  .contact-list svg { width: 10px; height: 10px; fill: var(--accent); }

  .address { position: absolute; right: 34px; top: 184px; text-align: right; font-size: 12.5px; line-height: 21px; font-style: normal; }

  .pattern-field {
    position: absolute; inset: 0;
    background: linear-gradient(135deg, #5f6062 0%, #727375 50%, #6a6b6d 100%);
  }
  .card-back .brand { left: 300px; top: 160px; }
  .card-back .brand-name { color: var(--white); font-size: 30px; }
  .card-back .brand-square { width: 26px; height: 26px; }
</style>
</head>
<body>
  <section class="card card-front" aria-label="Business card front">
    <div class="brand">
      <span class="brand-square"></span>
      <span class="brand-name">Norvane</span>
    </div>
    <div class="holder">
      <div class="holder-name">DANA KELLER</div>
      <div class="holder-role">President</div>
    </div>
    <div class="divider"></div>
    <ul class="contact-list">
      <li><svg viewBox="0 0 10 10"><path d="M2 0.5 L4 2.5 L3 3.8 Q4.5 6 6.2 7 L7.5 6 L9.5 8 L8 9.5 Q3.5 9 0.5 2 Z"/></svg>555-014-2290</li>
      <li><svg viewBox="0 0 10 10"><rect x="0.5" y="2" width="9" height="6.5"/></svg>dkeller@norvane.com</li>
      <li><svg viewBox="0 0 10 10"><circle cx="5" cy="5" r="4.5"/></svg>www.norvane.com</li>
    </ul>
    <address class="address">
      1180 Harbor Crest Lane<br>
      Bayview CA 90412
    </address>
  </section>

  <section class="card card-back" aria-label="Business card back">
    <div class="pattern-field" role="img" aria-label="Embossed repeating brand pattern in grey tones"></div>
    <div class="brand">
      <span class="brand-square"></span>
      <span class="brand-name">Norvane</span>
    </div>
  </section>
</body>
</html>
```